RM Installations Web Site Design

Need a basic site to show clients a little about what we do. We are a custom audio video company in the high-end residential market. Need a few basic but professional pages to show past projects and products we sell. No e-commerce. Should include my new logo from MarkBazaar.

Industry/Entity Type

Residential

Number of Pages Required

2 page

Font styles to use
Serif
Sans Serif

Colors
f78f20

Requirements
Must have
• Company Logo, Send feedback page
Nice to have
• I have no ideas about design, but I do know what I like and dislike when I see it.

```html
<!DOCTYPE html>
<html lang="en">
<head>
<meta charset="utf-8">
<title>RM Installations</title>
<link rel="stylesheet" href="https://fonts.googleapis.com/css2?family=Oswald:wght@400;500&family=Open+Sans:wght@400;600;700&display=swap">
<style>
:root{
  --orange:#f78f20;
  --orange-dark:#e07a10;
  --charcoal:#3a3a3a;
  --ink:#333;
  --muted:#666;
  --light:#eeeeee;
  --white:#fff;
}
*{margin:0;padding:0;box-sizing:border-box}
html,body{width:667px;height:1200px;overflow:hidden}
body{font-family:"Open Sans",Arial,sans-serif;color:var(--ink);background:var(--white)}
.page{width:667px;height:1200px;position:relative}

/* top bar */
.topbar{height:18px;background:var(--charcoal);color:#ddd;font-size:8px;display:flex;align-items:center;padding:0 90px;gap:22px}
.topbar span{display:flex;align-items:center;gap:4px}

/* header */
.header{height:44px;display:flex;align-items:center;justify-content:space-between;padding:0 18px 0 88px;border-bottom:1px solid #ddd}
.brand{display:flex;align-items:center;gap:6px;font-weight:700;font-size:12px;color:var(--charcoal);text-transform:uppercase;letter-spacing:.3px}
.brand-square{width:18px;height:18px;background:var(--orange)}
.nav{display:flex;height:44px;align-items:stretch}
.nav a{font-size:8px;font-weight:600;color:var(--charcoal);text-decoration:none;display:flex;align-items:center;padding:0 8px;text-transform:uppercase}
.nav a.active{background:var(--orange);color:var(--white)}
.call-pill{position:absolute;right:18px;top:3px;background:var(--orange);color:#fff;font-size:8px;padding:1px 8px;border-radius:2px;font-weight:600}

/* hero */
.hero{height:223px;position:relative;background:linear-gradient(100deg,#d8d4cf 0%,#b9b5ae 35%,#8c7a66 55%,#c9b49a 75%,#efe8df 100%)}
.hero-title{position:absolute;left:0;right:0;bottom:14px;text-align:center;font-family:"Oswald",Arial,sans-serif;font-weight:500;font-size:33px;color:#fff;text-shadow:0 2px 4px rgba(0,0,0,.45)}
.hero-arrow{position:absolute;top:96px;width:16px;height:28px;background:rgba(0,0,0,.45);display:flex;align-items:center;justify-content:center}
.hero-arrow.left{left:0}.hero-arrow.right{right:0}

/* shared section bits */
.section{position:relative;text-align:center}
.mark{width:16px;height:16px;background:var(--orange);margin:0 auto}
.section-title{font-family:"Open Sans",Arial,sans-serif;font-weight:600;font-size:16px;margin-top:10px}
.section-title em{font-style:normal;color:var(--orange)}
.btn{display:inline-block;background:var(--orange);color:#fff;font-size:7px;font-weight:700;padding:4px 12px;text-transform:uppercase;border-radius:2px}

/* about */
.about{height:193px;padding-top:24px}
.about p{width:470px;margin:12px auto 0;font-size:7.5px;line-height:1.55;color:var(--muted)}
.about .btn{margin-top:16px}

/* services */
.services{height:226px;background:var(--orange);padding-top:24px;color:#fff}
.services::before,.products::before{content:"";position:absolute;left:50%;top:0;transform:translateX(-50%);border-left:14px solid transparent;border-right:14px solid transparent;border-top:10px solid var(--white)}
.products::before{border-top-color:var(--orange)}
.services .mark{background:#fff}
.services .section-title{color:#fff}
.service-row{display:flex;justify-content:center;gap:12px;margin-top:28px}
.service{width:68px;display:flex;flex-direction:column;align-items:center}
.service-icon{width:46px;height:46px;border-radius:50%;background:#fff;display:flex;align-items:center;justify-content:center}
.service-label{font-size:6.5px;line-height:1.3;margin-top:8px;font-weight:600}
.carousel-arrow{position:absolute;width:24px;height:24px;border-radius:50%;background:#fff;display:flex;align-items:center;justify-content:center}
.services .carousel-arrow{top:112px}
.carousel-arrow.left{left:72px}.carousel-arrow.right{right:72px}
.dots{display:flex;justify-content:center;gap:4px;margin-top:12px}
.dots i{width:5px;height:5px;border-radius:50%;background:rgba(255,255,255,.5)}
.dots i.on{background:#fff}

/* products */
.products{height:218px;background:var(--light);padding-top:22px}
.product-row{display:flex;justify-content:center;gap:10px;margin-top:16px}
.product{width:116px}
.product .thumb{height:80px}
.product .cap{font-size:6.5px;color:var(--orange);font-weight:600;margin-top:4px}
.products .carousel-arrow{top:106px;background:none}
.products .carousel-arrow.left{left:60px}.products .carousel-arrow.right{right:60px}
.products .btn{margin-top:12px}

/* projects */
.projects{height:220px;padding-top:26px}
.project-row{display:flex;justify-content:center;gap:12px;margin-top:36px}
.project{width:92px;height:94px;position:relative}
.project .num{position:absolute;top:-6px;right:-6px;width:16px;height:16px;border-radius:50%;background:var(--orange);color:#fff;font-size:8px;font-weight:700;display:flex;align-items:center;justify-content:center}
.project .overlay{position:absolute;left:0;right:0;top:28px;padding:4px;background:rgba(0,0,0,.45);color:#fff;font-size:6px;line-height:1.3}
.projects .carousel-arrow{top:124px;background:none}
.projects .carousel-arrow.left{left:86px}.projects .carousel-arrow.right{right:86px}

/* footer */
.footer-main{height:33px;background:var(--orange);display:flex;align-items:center;justify-content:space-between;padding:0 88px;position:relative}
.footer-nav{display:flex;gap:8px}
.footer-nav a{font-size:6.5px;color:#fff;text-decoration:none;font-weight:600;text-transform:uppercase;white-space:nowrap}
.footer-mark{position:absolute;left:388px;top:8px;width:16px;height:16px;background:#fff}
.follow{display:flex;align-items:center;gap:4px;color:#fff;font-size:8px}
.follow i{width:11px;height:11px;border-radius:50%;border:1px solid #fff}
.footer-base{height:18px;background:var(--charcoal);color:#bbb;font-size:6.5px;display:flex;align-items:center;padding:0 88px}
</style>
</head>
<body>
<div class="page">

  <div class="topbar">
    <span><svg width="7" height="7" viewBox="0 0 10 10"><path d="M2 1l2 2-1 1.5c.6 1.2 1.3 1.9 2.5 2.5L7 6l2 2-1.5 1.5C4 9 1 6 .5 2.5z" fill="#f78f20"/></svg>123.456.7890</span>
    <span><svg width="8" height="6" viewBox="0 0 10 7"><rect x=".5" y=".5" width="9" height="6" fill="none" stroke="#f78f20"/><path d="M.5.5l4.5 3.5 4.5-3.5" fill="none" stroke="#f78f20"/></svg>info@rminstallations.com</span>
  </div>

  <header class="header">
    <div class="brand"><span class="brand-square"></span>RM Installations</div>
    <nav class="nav">
      <a class="active" href="#">Home</a><a href="#">About</a><a href="#">What we do</a><a href="#">Products</a><a href="#">Past projects</a><a href="#">Contact</a>
    </nav>
  </header>
  <div class="call-pill">123.456.7890</div>

  <section class="hero" role="img" aria-label="Photo of a technician mounting a security camera on a home's exterior wall">
    <div class="hero-arrow left"><svg width="8" height="10"><path d="M7 0L1 5l6 5" fill="none" stroke="#fff" stroke-width="2"/></svg></div>
    <div class="hero-arrow right"><svg width="8" height="10"><path d="M1 0l6 5-6 5" fill="none" stroke="#fff" stroke-width="2"/></svg></div>
    <h1 class="hero-title">We Are Custom Audio Video Company</h1>
  </section>

  <section class="section about">
    <div class="mark"></div>
    <h2 class="section-title">About <em>RM Installations</em></h2>
    <p>We design and install custom audio, video, lighting and network systems for fine homes across the state. Every project is planned around the way you live, with clean wiring, simple controls and support that lasts long after the final walkthrough.</p>
    <span class="btn">Read more</span>
  </section>

  <section class="section services">
    <div class="mark"></div>
    <h2 class="section-title">Our services</h2>
    <div class="carousel-arrow left"><svg width="8" height="10"><path d="M7 0L1 5l6 5" fill="none" stroke="#3a3a3a" stroke-width="2"/></svg></div>
    <div class="carousel-arrow right"><svg width="8" height="10"><path d="M1 0l6 5-6 5" fill="none" stroke="#3a3a3a" stroke-width="2"/></svg></div>
    <div class="service-row">
      <div class="service">
        <div class="service-icon"><svg width="24" height="24" viewBox="0 0 24 24"><path d="M3 9h4l6-5v16l-6-5H3z" fill="#3a3a3a"/><path d="M16 8a5 5 0 0 1 0 8M18.5 5.5a8.5 8.5 0 0 1 0 13" fill="none" stroke="#3a3a3a" stroke-width="1.6"/></svg></div>
        <div class="service-label">Distributed Video</div>
      </div>
      <div class="service">
        <div class="service-icon"><svg width="24" height="24" viewBox="0 0 24 24"><rect x="3" y="7" width="14" height="8" rx="1" fill="#3a3a3a" transform="rotate(-12 10 11)"/><path d="M9 15v5h6" fill="none" stroke="#3a3a3a" stroke-width="1.6"/><circle cx="19" cy="9" r="2" fill="#3a3a3a"/></svg></div>
        <div class="service-label">Security Camera Systems</div>
      </div>
      <div class="service">
        <div class="service-icon"><svg width="24" height="24" viewBox="0 0 24 24"><rect x="6" y="3" width="12" height="18" rx="1" fill="#3a3a3a"/><circle cx="12" cy="14" r="3.5" fill="#fff"/><circle cx="12" cy="7" r="1.5" fill="#fff"/></svg></div>
        <div class="service-label">Residential Cinemas</div>
      </div>
      <div class="service">
        <div class="service-icon"><svg width="24" height="24" viewBox="0 0 24 24"><circle cx="12" cy="12" r="4" fill="#3a3a3a"/><path d="M12 2v4M12 18v4M2 12h4M18 12h4M5 5l3 3M16 16l3 3M5 19l3-3M16 8l3-3" stroke="#3a3a3a" stroke-width="1.6"/></svg></div>
        <div class="service-label">Commercial Lighting Control</div>
      </div>
      <div class="service">
        <div class="service-icon"><svg width="24" height="24" viewBox="0 0 24 24"><path d="M4 15v-3a8 8 0 0 1 16 0v3" fill="none" stroke="#3a3a3a" stroke-width="2"/><rect x="3" y="14" width="5" height="7" rx="1" fill="#3a3a3a"/><rect x="16" y="14" width="5" height="7" rx="1" fill="#3a3a3a"/></svg></div>
        <div class="service-label">Outdoor Audio and Video</div>
      </div>
      <div class="service">
        <div class="service-icon"><svg width="24" height="24" viewBox="0 0 24 24"><rect x="9" y="2" width="6" height="5" fill="#3a3a3a"/><rect x="2" y="17" width="6" height="5" fill="#3a3a3a"/><rect x="9" y="17" width="6" height="5" fill="#3a3a3a"/><rect x="16" y="17" width="6" height="5" fill="#3a3a3a"/><path d="M12 7v10M5 17v-5h14v5" fill="none" stroke="#3a3a3a" stroke-width="1.4"/></svg></div>
        <div class="service-label">Residential Computer Networks</div>
      </div>
    </div>
    <div class="dots"><i class="on"></i><i></i><i></i></div>
  </section>

  <section class="section products">
    <div class="mark"></div>
    <h2 class="section-title">Our <em>Products</em></h2>
    <div class="carousel-arrow left"><svg width="8" height="12"><path d="M7 0L1 6l6 6" fill="none" stroke="#555" stroke-width="2"/></svg></div>
    <div class="carousel-arrow right"><svg width="8" height="12"><path d="M1 0l6 6-6 6" fill="none" stroke="#555" stroke-width="2"/></svg></div>
    <div class="product-row">
      <div class="product"><div class="thumb" role="img" aria-label="Photo of security camera monitors" style="background:linear-gradient(135deg,#2b2b2b,#6e6e6e 60%,#c9c9c9)"></div><div class="cap">Security Camera Systems</div></div>
      <div class="product"><div class="thumb" role="img" aria-label="Photo of a home media room with red seating" style="background:linear-gradient(135deg,#4a1010,#a8282a 55%,#3a2a22)"></div><div class="cap">Media Rooms</div></div>
      <div class="product"><div class="thumb" role="img" aria-label="Photo of an outdoor television on a patio" style="background:linear-gradient(135deg,#6b5a3c,#a8916a 50%,#4f6a3a)"></div><div class="cap">Outdoor Audio and Video</div></div>
      <div class="product"><div class="thumb" role="img" aria-label="Photo of a tablet controlling home lighting" style="background:linear-gradient(135deg,#3b2f25,#8a6f4e 55%,#d2b88c)"></div><div class="cap">Automated Lighting Control</div></div>
    </div>
    <span class="btn">See all</span>
  </section>

  <section class="section projects">
    <div class="mark"></div>
    <h2 class="section-title">Past <em>Projects</em></h2>
    <div class="carousel-arrow left"><svg width="8" height="12"><path d="M7 0L1 6l6 6" fill="none" stroke="#555" stroke-width="2"/></svg></div>
    <div class="carousel-arrow right"><svg width="8" height="12"><path d="M1 0l6 6-6 6" fill="none" stroke="#555" stroke-width="2"/></svg></div>
    <div class="project-row">
      <div class="project" role="img" aria-label="Photo of a finished home theater project" style="background:linear-gradient(135deg,#5a4632,#a07a52)"><div class="overlay">Whole home audio and a private cinema room</div><span class="num">1</span></div>
      <div class="project" role="img" aria-label="Photo of a client using a home control touchscreen" style="background:linear-gradient(135deg,#7d8a96,#c7ccd1)"><span class="num">2</span></div>
      <div class="project" role="img" aria-label="Photo of wall mounted lighting keypads" style="background:linear-gradient(135deg,#9aa3a8,#e3e6e8)"><span class="num">3</span></div>
      <div class="project" role="img" aria-label="Photo of an installer holding equipment" style="background:linear-gradient(135deg,#3f5f86,#d9a85a)"><span class="num">4</span></div>
    </div>
  </section>

  <footer>
    <div class="footer-main">
      <nav class="footer-nav"><a href="#">Home</a><a href="#">About</a><a href="#">What we do</a><a href="#">Products</a><a href="#">Past projects</a><a href="#">Contact</a></nav>
      <span class="footer-mark"></span>
      <div class="follow">Follow us on <i></i><i></i><i></i><i></i><i></i></div>
    </div>
    <div class="footer-base">© 2015 RM Installations. All Rights Reserved.</div>
  </footer>

</div>
</body>
</html>
```